New business stationairy

I need paper with header and footer and business cards.
I am a Ltd Company and my main field of expertise is QA/QC inspection in the Oil and Gas Industry. I will need all contact detail inserted and a footer with registration number and bank details etc

```html
<!DOCTYPE html>
<html lang="en">
<head>
<meta charset="utf-8">
<title>Halden Inspection Services – Business Card Options</title>
<link rel="stylesheet" href="https://fonts.googleapis.com/css2?family=Michroma&family=Encode+Sans+Condensed:wght@400;500&family=Open+Sans:wght@400&display=swap">
<style>
  :root {
    --navy: #232a7c;
    --navy-deep: #262a78;
    --band-blue: #233a82;
    --red: #c1272d;
    --faint: #dcdce8;
    --faint-dark: #3e4390;
    --ink: #222;
    --label: #ffffff;
    --board-light: #8c8c8c;
    --board-dark: #565656;
  }
  * { box-sizing: border-box; margin: 0; padding: 0; }
  html, body { width: 1200px; height: 1000px; overflow: hidden; }
  body {
    position: relative;
    background: radial-gradient(ellipse at 20% 5%, var(--board-light) 0%, #6c6c6c 50%, var(--board-dark) 100%);
    font-family: "Encode Sans Condensed", "Arial Narrow", sans-serif;
  }
  .card {
    position: absolute;
    width: 375px; height: 249px;
    background: #fff;
    overflow: hidden;
  }
  .card--small { width: 314px; height: 207px; }
  .card--dark { background: var(--navy-deep); }

  .holder-name {
    position: absolute; left: 167px; top: 30px;
    font-family: "Michroma", sans-serif;
    font-size: 14px; letter-spacing: 0.5px;
    color: var(--red);
    white-space: nowrap;
  }
  .holder-name--navy { color: var(--navy); }
  .holder-name--light { color: #fff; }
  .holder-role {
    position: absolute; left: 167px; top: 49px;
    font-family: "Open Sans", sans-serif; font-size: 8px; color: var(--ink);
  }
  .card--small .holder-name { left: 140px; top: 25px; font-size: 12px; }
  .card--small .holder-role { left: 140px; top: 40px; font-size: 7px; }
  .card--dark .holder-role { color: #e6e6f0; }

  .brand-watermark {
    position: absolute; right: 20px; top: 92px;
    font-family: "Encode Sans Condensed", sans-serif; font-weight: 500;
    font-size: 68px; line-height: 1;
    color: var(--faint);
  }
  .card--small .brand-watermark { right: 14px; top: 86px; font-size: 56px; }
  .card--dark .brand-watermark { color: var(--faint-dark); }

  .contact-list {
    position: absolute; left: 32px; top: 162px;
    list-style: none;
    font-size: 9.5px; line-height: 16px; color: var(--ink);
  }
  .contact-list li { display: flex; align-items: flex-start; gap: 5px; }
  .contact-list svg { width: 10px; height: 10px; margin-top: 3px; flex: none; }
  .contact-list .address { line-height: 12px; padding-top: 2px; }
  .card--small .contact-list { left: 26px; top: 118px; font-size: 8px; line-height: 14px; }
  .card--small .contact-list svg { width: 9px; height: 9px; }
  .card--small .contact-list .address { line-height: 10px; }
  .card--dark .contact-list { color: #fff; }

  .company-lockup {
    position: absolute; left: 0; right: 0; top: 112px;
    display: flex; align-items: center; justify-content: center; gap: 10px;
  }
  .company-name {
    font-family: "Encode Sans Condensed", sans-serif; font-weight: 400;
    font-size: 24px; color: var(--navy); white-space: nowrap;
  }
  .company-dot { width: 12px; height: 12px; border-radius: 50%; background: var(--red); flex: none; }
  .card--small .company-lockup { top: 86px; }
  .card--small .company-name { font-size: 20px; }

  .edge-band { position: absolute; left: 0; bottom: 0; width: 100%; display: block; }

  .card-label {
    position: absolute;
    font-family: "Open Sans", Arial, sans-serif; font-size: 17px;
    color: var(--label); transform: translateX(-50%); white-space: nowrap;
  }
</style>
</head>
<body>

<svg width="0" height="0" style="position:absolute" aria-hidden="true">
  <defs>
    <symbol id="icon-phone" viewBox="0 0 10 10">
      <rect width="10" height="10" rx="2" fill="#232a7c"/>
      <rect x="3" y="1.6" width="4" height="6.8" rx="0.8" fill="#fff"/>
      <rect x="3.7" y="2.4" width="2.6" height="4" fill="#232a7c"/>
    </symbol>
    <symbol id="icon-mail" viewBox="0 0 10 10">
      <rect width="10" height="10" rx="2" fill="#232a7c"/>
      <rect x="2" y="3" width="6" height="4.4" fill="#fff"/>
      <path d="M2 3 L5 5.6 L8 3" fill="none" stroke="#232a7c" stroke-width="0.7"/>
    </symbol>
    <symbol id="icon-pin" viewBox="0 0 10 10">
      <rect width="10" height="10" rx="2" fill="#232a7c"/>
      <path d="M5 8.6 C3 6.2 2.6 5 2.6 4.2 A2.4 2.4 0 0 1 7.4 4.2 C7.4 5 7 6.2 5 8.6Z" fill="#fff"/>
      <circle cx="5" cy="4.2" r="0.9" fill="#232a7c"/>
    </symbol>
    <symbol id="icon-phone-light" viewBox="0 0 10 10">
      <rect width="10" height="10" rx="2" fill="#fff"/>
      <rect x="3" y="1.6" width="4" height="6.8" rx="0.8" fill="#262a78"/>
      <rect x="3.7" y="2.4" width="2.6" height="4" fill="#fff"/>
    </symbol>
    <symbol id="icon-mail-light" viewBox="0 0 10 10">
      <rect width="10" height="10" rx="2" fill="#fff"/>
      <rect x="2" y="3" width="6" height="4.4" fill="#262a78"/>
      <path d="M2 3 L5 5.6 L8 3" fill="none" stroke="#fff" stroke-width="0.7"/>
    </symbol>
    <symbol id="icon-pin-light" viewBox="0 0 10 10">
      <rect width="10" height="10" rx="2" fill="#fff"/>
      <path d="M5 8.6 C3 6.2 2.6 5 2.6 4.2 A2.4 2.4 0 0 1 7.4 4.2 C7.4 5 7 6.2 5 8.6Z" fill="#262a78"/>
      <circle cx="5" cy="4.2" r="0.9" fill="#fff"/>
    </symbol>
  </defs>
</svg>

<!-- Option 1 -->
<section class="card front" style="left:208px; top:66px;">
  <div class="holder-name">Maria Halden</div>
  <div class="holder-role">Owner</div>
  <div class="brand-watermark">Halden</div>
  <ul class="contact-list">
    <li><svg><use href="#icon-phone"/></svg>07700 900417</li>
    <li><svg><use href="#icon-mail"/></svg>info@haldeninspect.co.uk</li>
    <li><svg><use href="#icon-pin"/></svg><span class="address">The Willows, Mill Road, Ashby<br>Fenwick Vale, Dorset, DT9 4QX</span></li>
  </ul>
  <svg class="edge-band" viewBox="0 0 375 12" height="12">
    <path d="M0 3 H232 Q244 3 248 12 H0Z" fill="var(--band-blue)"/>
    <path d="M249 3 H375 V12 H257 Q255 5 249 3Z" fill="var(--red)"/>
  </svg>
</section>
<div class="card-label" style="left:367px; top:325px;">Front 1</div>

<section class="card back" style="left:629px; top:66px;">
  <div class="company-lockup"><span class="company-dot"></span><span class="company-name">Halden Inspection Services Ltd</span></div>
  <svg class="edge-band" viewBox="0 0 375 12" height="12">
    <path d="M0 3 H232 Q244 3 248 12 H0Z" fill="var(--band-blue)"/>
    <path d="M249 3 H375 V12 H257 Q255 5 249 3Z" fill="var(--red)"/>
  </svg>
</section>
<div class="card-label" style="left:816px; top:321px;">Back 1</div>

<!-- Option 2 -->
<section class="card front" style="left:208px; top:359px;">
  <div class="holder-name holder-name--navy">Maria Halden</div>
  <div class="holder-role">Owner</div>
  <div class="brand-watermark">Halden</div>
  <ul class="contact-list">
    <li><svg><use href="#icon-phone"/></svg>07700 900417</li>
    <li><svg><use href="#icon-mail"/></svg>info@haldeninspect.co.uk</li>
    <li><svg><use href="#icon-pin"/></svg><span class="address">The Willows, Mill Road, Ashby<br>Fenwick Vale, Dorset, DT9 4QX</span></li>
  </ul>
</section>
<div class="card-label" style="left:382px; top:620px;">Front 2</div>

<section class="card back" style="left:629px; top:359px;">
  <div class="company-lockup"><span class="company-dot"></span><span class="company-name">Halden Inspection Services Ltd</span></div>
</section>
<div class="card-label" style="left:813px; top:613px;">Back 2</div>

<!-- Option 3 -->
<section class="card card--small front" style="left:81px; top:651px;">
  <div class="holder-name">Maria Halden</div>
  <div class="holder-role">Owner</div>
  <div class="brand-watermark">Halden</div>
  <ul class="contact-list">
    <li><svg><use href="#icon-phone"/></svg>07700 900417</li>
    <li><svg><use href="#icon-mail"/></svg>info@haldeninspect.co.uk</li>
    <li><svg><use href="#icon-pin"/></svg><span class="address">The Willows, Mill Road, Ashby<br>Fenwick Vale, Dorset, DT9 4QX</span></li>
  </ul>
  <svg class="edge-band" viewBox="0 0 314 32" height="32">
    <path d="M0 16 Q90 2 180 14 T314 18 V32 H0Z" fill="var(--band-blue)"/>
    <path d="M0 12 Q90 -2 180 10 T314 16" fill="none" stroke="var(--red)" stroke-width="3"/>
  </svg>
</section>
<div class="card-label" style="left:268px; top:874px;">Front 3</div>

<section class="card card--small back" style="left:426px; top:651px;">
  <div class="company-lockup"><span class="company-dot"></span><span class="company-name">Halden Inspection Services Ltd</span></div>
  <svg class="edge-band" viewBox="0 0 314 32" height="32">
    <path d="M0 16 Q90 2 180 14 T314 18 V32 H0Z" fill="var(--band-blue)"/>
    <path d="M0 12 Q90 -2 180 10 T314 16" fill="none" stroke="var(--red)" stroke-width="3"/>
  </svg>
</section>
<div class="card-label" style="left:583px; top:874px;">Back 3</div>

<!-- Option 4 -->
<section class="card card--small card--dark front" style="left:797px; top:651px;">
  <div class="holder-name holder-name--light">Maria Halden</div>
  <div class="holder-role">Owner</div>
  <div class="brand-watermark">Halden</div>
  <ul class="contact-list" style="top:135px;">
    <li><svg><use href="#icon-phone-light"/></svg>07700 900417</li>
    <li><svg><use href="#icon-mail-light"/></svg>info@haldeninspect.co.uk</li>
    <li><svg><use href="#icon-pin-light"/></svg><span class="address">The Willows, Mill Road, Ashby<br>Fenwick Vale, Dorset, DT9 4QX</span></li>
  </ul>
</section>
<div class="card-label" style="left:903px; top:874px;">Front 4</div>

</body>
</html>
```